4th Generation Family Business Needs a New Card Design!

We are a family owned 4th Generation company. We are based in the Sydney, Australia area and we are desperately in need of a more modern and classy card. We are monumental masons who design, supply & erect lasting memorials throughout cemeteries in Sydney. Our customers are normally in a period of grieving. I have attached logo files that will need to be implemented on the card. Company was established 1935. Australian Owned and Operated. Card needs to be designed to PIXO.com specification.

Target Market(s)

Our target market is based upon people that a grieving for family members that have passed away. We also deal with alot of companies that own and operate cemeteries.

Industry/Entity Type

Business

Contact Information for Business Card

Simon Harcourt, Operations Manager, 0417293086, simon@harcourtmemorials.com.au
Lewis Harcourt, Director, 0491630572, lewis@harcourtmemorials.com.au
Phone # 02 9561 3048
Website: www.harcourtmemorials.com.au
Address: Suite 17, 8 Palfrey Lane, West Carlow, Sydney NSW 2156

Font styles to use
Serif
Decorative
Script

Requirements
Must have
• Would like to see the logo nicely implemented with a modern design. Embossed lettering would be a nice additive.

```html
<!DOCTYPE html>
<html lang="en">
<head>
<meta charset="utf-8">
<title>Harcourt Memorials — Business Cards</title>
<link rel="stylesheet" href="https://fonts.googleapis.com/css2?family=Arimo:wght@400;700&display=swap">
<style>
  :root {
    --backdrop: #d9d9d9;
    --card: #f7f7f7;
    --ink: #1f1c1a;
    --ink-soft: #3a3a3a;
    --muted: #6b6b6b;
    --gold: #e2b526;
  }
  * { margin: 0; padding: 0; box-sizing: border-box; }
  html, body { width: 1200px; height: 864px; overflow: hidden; }
  body {
    background: var(--backdrop);
    font-family: "Arimo", Arial, sans-serif;
    color: var(--ink);
    position: relative;
  }
  .card {
    position: absolute;
    width: 560px;
    height: 342px;
    background: var(--card);
    box-shadow: 0 6px 18px rgba(0,0,0,0.18);
    display: flex;
    flex-direction: column;
    align-items: center;
    justify-content: center;
    text-align: center;
  }
  .card--front { left: 580px; top: 70px; }
  .card--contact { left: 60px; top: 452px; justify-content: flex-start; padding-top: 36px; }

  .brand {
    display: flex;
    align-items: center;
    gap: 12px;
  }
  .brand__mark {
    width: 18px; height: 18px;
    background: var(--gold);
  }
  .brand__name {
    font-weight: 700;
    color: var(--ink);
    letter-spacing: 0.04em;
    text-transform: uppercase;
  }
  .card--front .brand__name { font-size: 36px; }
  .card--contact .brand__name { font-size: 26px; }
  .card--contact .brand__mark { width: 14px; height: 14px; }

  .people {
    display: flex;
    align-items: stretch;
    margin-top: 22px;
  }
  .person { padding: 0 10px; }
  .person + .person { border-left: 1.5px solid var(--ink); }
  .person__name { font-size: 17px; color: var(--ink); }
  .person__role { font-size: 11px; color: var(--muted); margin-top: 1px; }

  .details {
    list-style: none;
    margin-top: 12px;
    font-size: 14.5px;
    line-height: 1.3;
    color: var(--ink-soft);
  }
</style>
</head>
<body>
  <section class="card card--front" aria-label="Card front">
    <div class="brand">
      <span class="brand__mark"></span>
      <span class="brand__name">Harcourt Memorials</span>
    </div>
  </section>

  <section class="card card--contact" aria-label="Card back">
    <div class="brand">
      <span class="brand__mark"></span>
      <span class="brand__name">Harcourt Memorials</span>
    </div>
    <div class="people">
      <div class="person">
        <div class="person__name">Simon Harcourt</div>
        <div class="person__role">Operations Manager</div>
      </div>
      <div class="person">
        <div class="person__name">Lewis Harcourt</div>
        <div class="person__role">Director</div>
      </div>
    </div>
    <ul class="details">
      <li>0417293086 / 0491630572</li>
      <li>02 9561 3048</li>
      <li>simon@harcourtmemorials.com.au</li>
      <li>lewis@harcourtmemorials.com.au</li>
      <li>www.harcourtmemorials.com.au</li>
      <li>Suite 17, 8 Palfrey Lane, West Carlow, Sydney NSW 2156</li>
    </ul>
  </section>
</body>
</html>
```